Design logo, business cards, and web page for new web and bi development consulting company

I've started a Web and Business Intelligence development consulting company. We develop on Quordex's stack, Visual Sudio and SQL Server. We develop responsive web sites and business intelligence platforms. I plan on focusing on small to medium sized business as my client base. I need a logo, business cards, and a one page web site. We will do more with the web site with you in the next six months if the business survives. The name of the company is Corvalo Integration Solutions, Corvalo for short.

Target Market(s)

small to medium sized businesses

Industry/Entity Type

Business

Contact Information for Business Card

logo
name
title
email
phone

Logo Text

Corvalo Integration Solutions - web and data solutions

Coding

Coded - Design and coding required

Number of Pages Required

1 page

Font styles to use
Sans Serif

Colors
0355a3
0092cd
00a88f
6b449b

Requirements
Nice to have
• web and data solutions

```html
<!DOCTYPE html>
<html lang="en">
<head>
<meta charset="utf-8">
<title>Corvalo Integration Solutions</title>
<link href="https://fonts.googleapis.com/css2?family=Open+Sans:wght@300;400;600;700&display=swap" rel="stylesheet">
<style>
:root{
  --blue:#0355a3;
  --bright:#1673d8;
  --sky:#0092cd;
  --ink:#333333;
  --muted:#8a8a8a;
  --line:#e3e3e3;
  --band:#e6e6e6;
  --dark:#4d4d4d;
  --darker:#303030;
  --white:#ffffff;
  --hero-a:#0d1a2c;
  --hero-b:#3a5470;
}
*{box-sizing:border-box;margin:0;padding:0}
html,body{width:1200px;height:3468px;overflow:hidden}
body{position:relative;font-family:"Open Sans",Arial,sans-serif;color:var(--ink);background:var(--white)}
.abs{position:absolute}

/* hero */
.hero{position:absolute;left:0;top:0;width:1200px;height:814px;overflow:hidden}
.hero-bg{position:absolute;inset:0;background:radial-gradient(ellipse at 30% 55%,#5c7896 0%,var(--hero-b) 35%,var(--hero-a) 100%)}
.brand{position:absolute;left:102px;top:26px;color:var(--white);font-weight:600;line-height:1}
.brand-name{font-size:40px;letter-spacing:1px}
.brand-sub{font-size:19px;margin-top:4px}
.nav{position:absolute;left:365px;top:44px;display:flex;gap:0;width:740px;justify-content:space-between}
.nav a{color:var(--white);text-decoration:none;font-size:13px;letter-spacing:.3px}
.hero-title{position:absolute;right:100px;top:282px;text-align:right;color:var(--white);font-weight:400;font-size:50px;line-height:70px;letter-spacing:1px}
.hero-text{position:absolute;right:100px;top:420px;width:580px;text-align:right;color:var(--white);font-size:13px;line-height:18px}
.btn{position:absolute;display:flex;align-items:center;justify-content:center;font-size:14px;color:var(--white);border-radius:3px}
.btn-ghost{left:751px;top:508px;width:167px;height:54px;border:2px solid var(--white)}
.btn-solid{left:936px;top:508px;width:164px;height:54px;background:var(--bright)}
.slide-arrow{position:absolute;top:370px;width:46px;height:46px;background:var(--bright);display:flex;align-items:center;justify-content:center}
.dots{position:absolute;left:568px;top:745px;display:flex;gap:6px}
.dots span{width:16px;height:16px;border-radius:50%;background:rgba(255,255,255,.75)}

/* services */
.section-title{position:absolute;left:0;width:1200px;text-align:center;font-weight:400;color:var(--ink)}
.services-title{top:836px;font-size:34px}
.divider{position:absolute;left:540px;top:900px;width:120px;height:30px}
.services-lead{position:absolute;left:320px;top:962px;width:560px;text-align:center;color:var(--muted);font-size:15px;line-height:24px;text-transform:uppercase}
.service{position:absolute;top:1080px;width:240px;text-align:center}
.service svg{display:block;margin:0 auto}
.service h3{font-weight:400;font-size:17px;margin-top:18px;color:#444}
.service p{font-size:11.5px;line-height:17px;color:var(--muted);margin:16px auto 0;width:230px}
.service .more{display:inline-block;margin-top:20px;background:#333;color:var(--white);font-size:9px;padding:9px 18px}

/* about */
.about{position:absolute;left:0;top:1392px;width:1200px;height:458px;background:var(--band);text-align:center}
.about h2{font-weight:300;font-size:70px;margin-top:40px;line-height:80px;color:#333}
.about .about-lead{font-weight:400;font-size:56px;color:var(--bright);line-height:64px;margin-top:8px}
.about .about-sub{font-size:30px;font-weight:400;color:#444;line-height:34px}
.about p{font-size:12.5px;line-height:19px;width:1000px;margin:10px auto 0;color:#333}
.about .btn-solid{left:502px;top:340px;width:198px;height:58px;font-size:14px}

/* news and testimonials */
.block-title{position:absolute;font-size:18px;font-weight:400;color:#333}
.block-rule{position:absolute;height:1px;background:var(--line)}
.block-rule span{position:absolute;left:0;top:-1px;width:80px;height:3px;background:var(--bright)}
.news-item{position:absolute;left:99px;width:480px}
.news-thumb{position:absolute;left:0;top:0;width:111px;height:111px}
.news-body{position:absolute;left:139px;top:0;width:340px}
.news-body h4{font-weight:400;font-size:17px;color:var(--blue);margin-top:6px}
.news-meta{font-size:10px;color:var(--muted);margin-top:6px}
.news-meta em{font-style:normal;color:var(--sky)}
.news-body p{font-size:11px;line-height:16px;color:#666;margin-top:8px}
.quote-box{position:absolute;left:617px;top:1988px;width:483px;height:158px;border:1px solid var(--line)}
.quote-mark{position:absolute;left:18px;top:22px;width:30px;height:30px;background:var(--blue);color:var(--white);font-size:26px;line-height:36px;text-align:center;font-weight:700}
.quote-box p{position:absolute;left:74px;top:26px;width:390px;font-size:11.5px;line-height:20px;color:var(--muted)}
.quote-tail{position:absolute;left:30px;top:2145px;width:0;height:0;border-left:10px solid transparent;border-right:10px solid transparent;border-top:10px solid var(--line)}
.quoter-avatar{position:absolute;left:617px;top:2173px;width:51px;height:51px;background:linear-gradient(#7d8793,#3e4650)}
.quoter-name{position:absolute;left:692px;top:2190px;font-size:11px;color:#444}
.quoter-role{position:absolute;left:692px;top:2206px;font-size:10px;color:var(--sky)}
.pager{position:absolute;top:1905px;width:20px;height:20px;border:1px solid var(--line)}

/* team */
.card{position:absolute;top:2354px;width:223px;height:328px;border:1px solid var(--line);background:var(--white)}
.card-photo{position:absolute;left:0;top:0;width:221px;height:224px;background:linear-gradient(180deg,#d6d6d6 0%,#c2c2c2 60%,#8a8f96 100%)}
.card h5{position:absolute;left:16px;top:240px;font-weight:400;font-size:13px;color:#444}
.card .role{position:absolute;left:16px;top:260px;font-size:10px;color:var(--sky)}
.card .card-rule{position:absolute;left:0;top:284px;width:221px;height:1px;background:var(--line)}
.card .social{position:absolute;left:16px;top:298px;display:flex;gap:14px}
.card .social span{width:11px;height:11px;border-radius:50%;background:#c6c6c6}

/* map */
.map{position:absolute;left:0;top:2735px;width:1200px;height:358px;background:linear-gradient(135deg,#efe9dc 0%,#e4e2d8 45%,#b7d3e8 75%,#cfe0ea 100%)}

/* footer */
.footer{position:absolute;left:0;top:3093px;width:1200px;height:324px;background:var(--dark);color:var(--white)}
.contact{position:absolute;top:62px}
.contact h6{font-size:30px;font-weight:400;display:flex;align-items:center;gap:8px;line-height:40px}
.contact p{font-size:14px;line-height:19px;margin-top:10px}
.footer-social{position:absolute;left:475px;top:232px;display:flex;gap:32px}
.footer-social span{width:26px;height:26px;border-radius:50%;background:var(--white)}
.copyright{position:absolute;left:0;top:3417px;width:1200px;height:51px;background:var(--darker);color:#ddd;font-size:11px;line-height:51px;padding-left:99px}
</style>
</head>
<body>

<header class="hero">
  <div class="hero-bg" role="img" aria-label="Photo of a businessman touching a glowing digital interface of hexagon icons"></div>
  <div class="brand">
    <div class="brand-name">Corvalo</div>
    <div class="brand-sub">Integration Solutions</div>
  </div>
  <nav class="nav">
    <a>HOME</a><a>ABOUT</a><a>OUR TEAM</a><a>WORK</a><a>PRICING</a><a>SERVICES</a><a>BLOG</a><a>FEATURES</a><a>CONTACT</a>
  </nav>
  <div class="slide-arrow" style="left:0">
    <svg width="16" height="16" viewBox="0 0 16 16"><path d="M10 2 L4 8 L10 14" stroke="#fff" stroke-width="2.5" fill="none"/></svg>
  </div>
  <div class="slide-arrow" style="right:0">
    <svg width="16" height="16" viewBox="0 0 16 16"><path d="M6 2 L12 8 L6 14" stroke="#fff" stroke-width="2.5" fill="none"/></svg>
  </div>
  <h1 class="hero-title">TALENTED TEAM OF<br>DEVELOPERS</h1>
  <p class="hero-text">Lorem Ipsum is simply dummy text of the printing and typesetting industry. Lorem Ipsum has been the industry's standard dummy text ever since the 1500s, when an unknown printer took a galley of type and scrambled it to make a type specimen book.</p>
  <div class="btn btn-ghost">LEARN MORE</div>
  <div class="btn btn-solid">DOWNLOAD</div>
  <div class="dots"><span></span><span></span><span></span></div>
</header>

<h2 class="section-title services-title">OUR SERVICES</h2>
<svg class="divider" viewBox="0 0 120 30">
  <line x1="0" y1="22" x2="46" y2="22" stroke="#d0d0d0"/>
  <line x1="74" y1="22" x2="120" y2="22" stroke="#d0d0d0"/>
  <path d="M53 8 L67 22 M67 8 L53 22" stroke="#0355a3" stroke-width="3"/>
</svg>
<p class="services-lead">Check out some of our main core features. Corvalo is a very powerful theme packed with tons of shortcodes</p>

<div class="service" style="left:93px">
  <svg width="48" height="48" viewBox="0 0 48 48" fill="none" stroke="#222" stroke-width="2">
    <path d="M10 20 a8 8 0 0 1 8-10 a10 10 0 0 1 18 2 a7 7 0 0 1 2 14 H12 a6 6 0 0 1-2-6z" fill="#222"/>
    <rect x="16" y="28" width="16" height="5" rx="1"/><rect x="16" y="35" width="16" height="5" rx="1"/><rect x="16" y="42" width="16" height="5" rx="1"/>
  </svg>
  <h3>Data Integration</h3>
  <p>Lorem Ipsum is simply dummy text of the printing and typesetting industry. Lorem Ipsum has be industry's standard dummy.</p>
  <span class="more">READ MORE</span>
</div>
<div class="service" style="left:363px">
  <svg width="48" height="48" viewBox="0 0 48 48" fill="none" stroke="#222" stroke-width="2">
    <path d="M4 4 V44 H46"/><path d="M8 38 L16 24 L22 30 L30 12 L36 22 L44 16"/>
  </svg>
  <h3>Enterprise Reporting</h3>
  <p>Lorem Ipsum is simply dummy text of the printing and typesetting industry. Lorem Ipsum has be industry's standard dummy.</p>
  <span class="more">READ MORE</span>
</div>
<div class="service" style="left:615px">
  <svg width="48" height="48" viewBox="0 0 48 48">
    <path d="M22 6 A19 19 0 1 0 42 26 H22z" fill="#222"/><path d="M26 2 A19 19 0 0 1 46 22 H26z" fill="#222"/>
  </svg>
  <h3>Business Process Automation</h3>
  <p>Lorem Ipsum is simply dummy text of the printing and typesetting industry. Lorem Ipsum has be industry's standard dummy.</p>
  <span class="more">READ MORE</span>
</div>
<div class="service" style="left:870px">
  <svg width="60" height="48" viewBox="0 0 60 48" fill="none" stroke="#222" stroke-width="2">
    <rect x="14" y="4" width="40" height="26" rx="2"/><path d="M26 38 H42 M34 30 V38"/>
    <rect x="2" y="18" width="14" height="26" rx="2" fill="#fff"/><rect x="40" y="24" width="16" height="20" rx="2" fill="#fff"/>
  </svg>
  <h3>Responsive Web Apps</h3>
  <p>Lorem Ipsum is simply dummy text of the printing and typesetting industry. Lorem Ipsum has be industry's standard dummy.</p>
  <span class="more">READ MORE</span>
</div>

<section class="about">
  <h2>ABOUT</h2>
  <div class="about-lead">CREATING REALLY USER-FRIENDLY</div>
  <div class="about-sub">WEBSITES THAT WORK FOR YOUR BENEFIT</div>
  <p>Lorem Ipsum is simply dummy text of the printing and typesetting industry. Lorem Ipsum has been the industry's standard dummy text ever since the 1500s, when an unknown printer took a galley of type and scrambled it to make a type specimen book. Lorem Ipsum is simply dummy text of the printing and typesetting industry. Lorem Ipsum has been the industry's standard dummy text ever since the 1500s, when an unknown printer took a galley of type and scrambled it to make a type specimen book.</p>
  <div class="btn btn-solid">READ MORE</div>
</section>

<h3 class="block-title" style="left:99px;top:1903px">Latest News</h3>
<div class="block-rule" style="left:99px;top:1944px;width:481px"><span></span></div>
<h3 class="block-title" style="left:617px;top:1903px">Testimonials</h3>
<div class="block-rule" style="left:617px;top:1944px;width:483px"><span></span></div>
<div class="pager" style="left:1055px"></div>
<div class="pager" style="left:1079px"></div>

<article class="news-item" style="top:1984px">
  <div class="news-thumb" role="img" aria-label="Photo of a newspaper page with news headlines" style="background:linear-gradient(135deg,#1f4f9a,#0e2a5e)"></div>
  <div class="news-body">
    <h4>Little girl having her teeth checked</h4>
    <div class="news-meta">September 15, 2015 · <em>Comments (4)</em></div>
    <p>Cum sociis natoque penatibus et magnis dis parturient montes. Pro vel nibh et elit mollis commodo et nec augue. Mauris et justo eu lectus auctor porta vel at libero.</p>
  </div>
</article>
<article class="news-item" style="top:2115px">
  <div class="news-thumb" role="img" aria-label="Photo of printed latest news lettering" style="background:linear-gradient(135deg,#d8cf9a,#8b7f4a)"></div>
  <div class="news-body">
    <h4>Close-up of medical equipment</h4>
    <div class="news-meta">September 15, 2015 · <em>Comments (2)</em></div>
    <p>Cum sociis natoque penatibus et magnis dis parturient montes. Pro vel nibh et elit mollis commodo et nec augue. Mauris at justo eu lectus auctor porta vel at libero.</p>
  </div>
</article>

<div class="quote-box">
  <div class="quote-mark">“</div>
  <p>Cum sociis natoque penatibus et magnis dis parturient montes. Pro vel nibh et elit mollis commodo et nec augue. Mauris at justo eu lectus auctor porta vel at libero. Susce mattis tellus vel augue mollis ultrices. Suspendisse potenti.</p>
</div>
<div class="quote-tail" style="left:647px"></div>
<div class="quoter-avatar" role="img" aria-label="Portrait photo of the client"></div>
<div class="quoter-name">Owen Larkin</div>
<div class="quoter-role">CEO OF LUMORA</div>

<h3 class="block-title" style="left:99px;top:2272px">Our Team</h3>
<div class="block-rule" style="left:99px;top:2312px;width:1001px"><span></span></div>

<div class="card" style="left:99px">
  <div class="card-photo" role="img" aria-label="Portrait photo of team member Dorian Vale"></div>
  <h5>Dorian Vale</h5><div class="role">CEO OF LUMORA</div><div class="card-rule"></div>
  <div class="social"><span></span><span></span><span></span><span></span></div>
</div>
<div class="card" style="left:358px">
  <div class="card-photo" role="img" aria-label="Portrait photo of team member Marek Holt"></div>
  <h5>Marek Holt</h5><div class="role">CEO OF LUMORA</div><div class="card-rule"></div>
  <div class="social"><span></span><span></span><span></span><span></span></div>
</div>
<div class="card" style="left:617px">
  <div class="card-photo" role="img" aria-label="Portrait photo of team member Elias Crane"></div>
  <h5>Elias Crane</h5><div class="role">CEO OF LUMORA</div><div class="card-rule"></div>
  <div class="social"><span></span><span></span><span></span><span></span></div>
</div>
<div class="card" style="left:876px">
  <div class="card-photo" role="img" aria-label="Portrait photo of team member Soren Pike"></div>
  <h5>Soren Pike</h5><div class="role">CEO OF LUMORA</div><div class="card-rule"></div>
  <div class="social"><span></span><span></span><span></span><span></span></div>
</div>

<div class="map" role="img" aria-label="Street map of the office location"></div>

<footer class="footer">
  <div class="contact" style="left:109px">
    <h6><svg width="24" height="24" viewBox="0 0 24 24"><path d="M5 2 L9 2 L11 7 L8 9 A12 12 0 0 0 15 16 L17 13 L22 15 L22 19 A3 3 0 0 1 19 22 A17 17 0 0 1 2 5 A3 3 0 0 1 5 2z" fill="#fff"/></svg>Call</h6>
    <p>+100 555 0142</p>
  </div>
  <div class="contact" style="left:490px;width:212px;text-align:center">
    <h6 style="justify-content:center"><svg width="22" height="22" viewBox="0 0 22 22"><circle cx="11" cy="11" r="10" fill="#fff"/><path d="M11 4 A4 4 0 0 1 15 8 C15 11 11 17 11 17 C11 17 7 11 7 8 A4 4 0 0 1 11 4z" fill="#4d4d4d"/></svg>Visit</h6>
    <p>P.O. Box 4810<br>92 Harbor Line Ave.<br>Westbrook, ST 40217</p>
  </div>
  <div class="contact" style="right:113px;text-align:right">
    <h6 style="justify-content:flex-end"><svg width="26" height="20" viewBox="0 0 26 20"><rect x="1" y="1" width="24" height="18" fill="#fff"/><path d="M1 1 L13 11 L25 1" stroke="#4d4d4d" stroke-width="2" fill="none"/></svg>Email</h6>
    <p>hello@corvalo-mail.com</p>
  </div>
  <div class="footer-social"><span></span><span></span><span></span><span></span><span></span></div>
</footer>
<div class="copyright">Copyright © 2015 - All Rights Reserved</div>

</body>
</html>
```